Simple and Clean business card design

We would like the design to be simple clean and to incorporate our colors.

We are open to your design and talent, we have the dots in our logo as we think of it as data points and we connect data points for people.

We are open to see the great creative and clean design you bring to the table

Contact Information for Business Card

please include: name, position, email, phone and website

Font styles to use
Sans Serif

Requirements
Must have
• my colors incorporated, simplicity
Nice to have
• lots of white space, simplicity
Should not have
• complexicity/ complex art

```html
<!DOCTYPE html>
<html lang="en">
<head>
<meta charset="utf-8">
<title>Nodewell Business Card</title>
<link href="https://fonts.googleapis.com/css2?family=Montserrat:wght@400;500;600;700&display=swap" rel="stylesheet">
<style>
  :root {
    --stage: #2e2b28;
    --card: #1d1e20;
    --ink: #ffffff;
    --muted: #9a9b9e;
    --green: #34a853;
    --blue: #5b7fc1;
    --yellow: #f9bf1a;
    --red: #e94335;
    --rule: #d8d8d8;
  }
  * { box-sizing: border-box; margin: 0; padding: 0; }
  html, body {
    width: 1200px; height: 900px; overflow: hidden;
    background: var(--stage);
    font-family: "Montserrat", sans-serif;
    color: var(--ink);
  }
  .canvas {
    width: 1200px; height: 900px;
    display: flex; flex-direction: column;
    align-items: center; justify-content: center; gap: 30px;
  }
  .card {
    width: 640px; height: 366px;
    background: var(--card);
    position: relative;
    box-shadow: 0 14px 30px rgba(0,0,0,0.45);
  }
  /* Back face */
  .card-back {
    display: flex; flex-direction: column;
    align-items: center; justify-content: center;
  }
  .back-mark { display: flex; align-items: center; gap: 14px; }
  .back-mark .dot {
    width: 34px; height: 34px; border-radius: 50%;
    background: var(--blue);
  }
  .back-mark .wordmark {
    font-weight: 700; font-size: 40px; letter-spacing: 0.01em;
    color: var(--ink);
  }
  .back-web {
    margin-top: 70px;
    font-size: 14px; letter-spacing: 0.32em;
    color: var(--muted);
  }
  /* Front face */
  .card-front { display: flex; align-items: center; }
  .front-brand {
    width: 318px; padding-left: 46px;
    display: flex; align-items: center; gap: 12px;
    margin-top: 70px;
  }
  .front-brand .dot {
    width: 30px; height: 30px; border-radius: 50%;
    background: var(--blue); flex: none;
  }
  .front-brand .wordmark {
    font-weight: 700; font-size: 46px; color: var(--ink);
    letter-spacing: -0.01em;
  }
  .divider {
    width: 1.5px; height: 200px; background: var(--rule);
    margin-top: 30px;
  }
  .details { padding-left: 22px; }
  .name {
    font-weight: 700; font-size: 24px; letter-spacing: 0.01em;
    text-transform: uppercase; line-height: 1;
  }
  .name .first { color: var(--green); }
  .role { font-size: 16px; font-weight: 500; margin-top: 6px; }
  .address { font-size: 12.5px; line-height: 1.4; margin-top: 16px; font-weight: 500; }
  .contacts { list-style: none; margin-top: 14px; }
  .contacts li {
    display: flex; align-items: center; gap: 10px;
    font-size: 13px; font-weight: 500; line-height: 1.55;
  }
  .contacts svg { width: 12px; height: 12px; flex: none; }
</style>
</head>
<body>
<main class="canvas">
  <section class="card card-back" aria-label="Card back">
    <div class="back-mark">
      <span class="dot"></span>
      <span class="wordmark">nodewell</span>
    </div>
    <p class="back-web">www.nodewell.one</p>
  </section>

  <section class="card card-front" aria-label="Card front">
    <div class="front-brand">
      <span class="dot"></span>
      <span class="wordmark">nodewell</span>
    </div>
    <div class="divider"></div>
    <div class="details">
      <h1 class="name"><span class="first">Marlo</span> Quinn</h1>
      <p class="role">Founder/ CEO</p>
      <p class="address">18 Alder Lane<br>Brookfield, OH 44403</p>
      <ul class="contacts">
        <li>
          <svg viewBox="0 0 24 24" fill="var(--green)" aria-hidden="true"><path d="M6.6 10.8a15 15 0 0 0 6.6 6.6l2.2-2.2a1 1 0 0 1 1-.25 11.4 11.4 0 0 0 3.6.57 1 1 0 0 1 1 1V20a1 1 0 0 1-1 1A17 17 0 0 1 3 4a1 1 0 0 1 1-1h3.5a1 1 0 0 1 1 1c0 1.25.2 2.45.57 3.57a1 1 0 0 1-.25 1z"/></svg>
          555-214-0386
        </li>
        <li>
          <svg viewBox="0 0 24 24" fill="var(--green)" aria-hidden="true"><path d="M2 5h20v14H2z M3 6l9 7 9-7" stroke="var(--card)" stroke-width="1.5"/></svg>
          marlo.quinn@nodewell.one
        </li>
        <li>
          <svg viewBox="0 0 24 24" aria-hidden="true"><circle cx="12" cy="12" r="10" fill="var(--green)"/><path d="M2 12h20M12 2c3 3 3 17 0 20M12 2c-3 3-3 17 0 20" stroke="var(--card)" stroke-width="1.4" fill="none"/></svg>
          www.nodewell.one
        </li>
      </ul>
    </div>
  </section>
</main>
</body>
</html>
```